KBT Business Cards

We require business cards for our business. We would like a matte black back to the card, with our logo centred in the middle. The front side of the card is open to design.

Target Market(s)

Clients looking for legal services (professional)

Industry/Entity Type

Legal

Contact Information for Business Card

Doran Kelbrath
Partner
Mobile: 0461 738 524
Email: doran@kbtlaw.co
Website: www.kbtlaw.co
Level 3, 118 Wendmore Street
Sydney NSW 2000

Font styles to use
Other font styles liked:
• Avenir

Colors
f04a50
ffffff
1b1b1b

Requirements
Must have
• Black back with logo included in the centre of the card.
• Our font is Avenir.

```html
<!DOCTYPE html>
<html lang="en">
<head>
<meta charset="utf-8">
<title>KBT Business Cards</title>
<link rel="stylesheet" href="https://fonts.googleapis.com/css2?family=Nunito+Sans:wght@400;600;700;800&display=swap">
<style>
  :root {
    --crimson: #e0234e;
    --crimson-deep: #a51d3c;
    --crimson-fold: #5e0f20;
    --ink: #1b1b1b;
    --black: #0d0d0d;
    --white: #ffffff;
    --stage: #262626;
    --plate-light: #2b2b2b;
    --plate-dark: #111111;
  }
  * { box-sizing: border-box; margin: 0; padding: 0; }
  html, body {
    width: 1200px; height: 960px; overflow: hidden;
    background: var(--stage);
    font-family: "Nunito Sans", "Avenir", sans-serif;
  }
  .canvas { position: relative; width: 1200px; height: 960px; }

  .card {
    position: absolute; left: 240px; width: 720px; height: 440px;
    overflow: hidden; border-radius: 4px;
    box-shadow: 0 14px 34px rgba(0,0,0,.45);
  }
  .card--back { top: 30px; }
  .card--front { top: 490px; background: var(--black); }

  /* back */
  .plate-texture {
    position: absolute; inset: 0;
    background: radial-gradient(ellipse at 45% 35%, var(--plate-light), var(--plate-dark) 75%);
  }
  .back-lockup {
    position: absolute; left: 50%; top: 150px; transform: translateX(-50%);
    display: flex; align-items: center; gap: 22px;
  }
  .mark-square { width: 70px; height: 70px; background: var(--crimson); flex: none; }
  .wordmark {
    font-weight: 800; font-size: 30px; line-height: 1.02; letter-spacing: .5px;
    text-transform: uppercase;
  }
  .wordmark--light { color: var(--white); }
  .wordmark--dark { color: var(--ink); font-size: 25px; }
  .back-web {
    position: absolute; left: 0; right: 0; top: 330px; text-align: center;
    color: var(--white); font-size: 15px; letter-spacing: 5px; font-weight: 600;
  }
  .back-web .accent { color: var(--crimson); }

  /* front */
  .front-brand {
    position: absolute; left: 0; top: 0; width: 318px; height: 100%;
    background: var(--white);
  }
  .front-lockup {
    position: absolute; left: 40px; top: 150px;
    display: flex; align-items: center; gap: 16px;
  }
  .front-lockup .mark-square { width: 54px; height: 54px; }

  .person { position: absolute; left: 350px; top: 52px; color: var(--white); }
  .person-name { font-weight: 800; font-size: 23px; letter-spacing: .6px; text-transform: uppercase; }
  .person-role { font-size: 13px; letter-spacing: 1px; text-transform: uppercase; margin-top: 2px; }

  .ribbon {
    position: absolute; left: 318px; right: 0;
    background: linear-gradient(90deg, var(--crimson), var(--crimson-deep));
    display: flex; align-items: center; gap: 16px; padding-left: 30px;
    color: var(--white); font-size: 16px; line-height: 1.35;
  }
  .ribbon::after {
    content: ""; position: absolute; left: 0; bottom: -14px;
    border-top: 14px solid var(--crimson-fold);
    border-left: 22px solid transparent;
  }
  .ribbon--address { top: 140px; height: 76px; }
  .ribbon--phone { top: 236px; height: 62px; font-size: 19px; letter-spacing: .5px; }
  .ribbon--web { top: 318px; height: 84px; }
  .icon-ring {
    width: 44px; height: 44px; border: 2px solid var(--white); border-radius: 50%;
    display: flex; align-items: center; justify-content: center; flex: none;
  }
  .icon-ring svg { width: 22px; height: 22px; }
</style>
</head>
<body>
<main class="canvas">

  <section class="card card--back" aria-label="Card back">
    <div class="plate-texture" role="img" aria-label="Matte black diamond tread plate texture"></div>
    <div class="back-lockup">
      <span class="mark-square"></span>
      <div class="wordmark wordmark--light">Kelbrath<br>Barrow<br>Tennant</div>
    </div>
    <p class="back-web">www.<span class="accent">kbtlaw</span>.co</p>
  </section>

  <section class="card card--front" aria-label="Card front">
    <div class="front-brand">
      <div class="front-lockup">
        <span class="mark-square"></span>
        <div class="wordmark wordmark--dark">Kelbrath<br>Barrow<br>Tennant</div>
      </div>
    </div>

    <div class="person">
      <p class="person-name">Doran Kelbrath</p>
      <p class="person-role">Partner</p>
    </div>

    <div class="ribbon ribbon--address">
      <span class="icon-ring">
        <svg viewBox="0 0 24 24" fill="none" stroke="#fff" stroke-width="2"><path d="M12 22s7-7.5 7-13a7 7 0 0 0-14 0c0 5.5 7 13 7 13z"/><circle cx="12" cy="9" r="2.5"/></svg>
      </span>
      <p>Level 3, 118 Wendmore Street<br>Sydney NSW 2000</p>
    </div>

    <div class="ribbon ribbon--phone">
      <span class="icon-ring">
        <svg viewBox="0 0 24 24" fill="none" stroke="#fff" stroke-width="2"><rect x="7" y="2" width="10" height="20" rx="2"/><line x1="11" y1="18" x2="13" y2="18"/></svg>
      </span>
      <p>0461 738 524</p>
    </div>

    <div class="ribbon ribbon--web">
      <span class="icon-ring">
        <svg viewBox="0 0 24 24" fill="none" stroke="#fff" stroke-width="1.8"><circle cx="12" cy="12" r="9"/><ellipse cx="12" cy="12" rx="4" ry="9"/><line x1="3" y1="12" x2="21" y2="12"/><path d="M5 7h14M5 17h14"/></svg>
      </span>
      <p>doran@kbtlaw.co<br>www.kbtlaw.co</p>
    </div>
  </section>

</main>
</body>
</html>
```